Redesign, cleanup and edit my Presentations

I have a series of power points that I use for training purposes. They were made by me over time. During the last couple years, I have evolved their look and content over time, but not consistently. More specifically, I have not gone back to re-edit the older decks. So, some decks are too wordy, too long, or and don't look consistent.

I am looking someone who can create a good design that I can use going forward, and who could also apply that theme to the existing decks, along with editing the existing, and future decks, too.

I have a lot of slides to produce and/or edit -approximately 500. But this request is a test to find a powerpoint partner. I am supplying 2 decks. One that's older and more wordy than the other. I would like to see what you would suggest we do differently. So that's what you are bidding on today. Also, you do not have to complete deck "Phase 7.4." I only need enough of the deck done to see where you would take it. Maybe 10 slides? Your choice. However, with that deck, there are lots of opportunities to clarify, re-align, and minimize within that deck.

But, if you are selected, I want to engage with you on an ongoing basis, and send more material your way. Then, you will be engaged to complete all decks.

Please ask me any questions to help you gain a better understanding of this project.

Target Market(s)

People in management, technical, medical, and financial fields who wish to become independent consultants.

Industry/Entity Type

Business Consultant

Font styles to use
Sans Serif

Requirements
Must have
• Use the existing color theme:
• yellow/gold - #f5b300,
• blue - 2b74a6
• Logo doesn't change
• Preferred fonts: Raleway for headings and Open Sans for general text
• Any pictures and graphics should have no copyright restrictions. That is, I should have use of the work without charge.
Nice to have
• I prefer a flat graphic style, although you can use pictures where it conveys a point more effectively.
• Ability to convert the presentations to Google Slides and Apple's Keynote apps.
• Ability to convert presentation to video
Should not have
• Restricted use graphics, photos, or other content.

```html
<!DOCTYPE html>
<html lang="en">
<head>
<meta charset="UTF-8">
<title>The elevator pitch</title>
<link rel="stylesheet" href="https://fonts.googleapis.com/css2?family=Raleway:wght@300;400;600&family=Open+Sans:wght@400;600&display=swap">
<style>
  :root {
    --brand-blue: #2b74a6;
    --blue-deep: #123049;
    --blue-night: #0c1f31;
    --gold: #f5b300;
    --gold-soft: #ffd45a;
    --photo-warm: #6b4a40;
    --photo-dark: #1d2027;
    --text-light: #f3f5f7;
  }
  * { margin: 0; padding: 0; box-sizing: border-box; }
  html, body {
    width: 1200px;
    height: 675px;
    overflow: hidden;
    background: var(--blue-night);
  }
  .slide {
    position: relative;
    width: 1200px;
    height: 675px;
    overflow: hidden;
    background:
      radial-gradient(ellipse at 90% 8%, rgba(43, 116, 166, 0.55), transparent 50%),
      radial-gradient(ellipse at 70% 75%, rgba(43, 116, 166, 0.25), transparent 55%),
      linear-gradient(160deg, var(--blue-deep) 0%, var(--blue-night) 100%);
  }
  .hero-photo {
    position: absolute;
    left: 0;
    top: 0;
    width: 616px;
    height: 675px;
    background:
      radial-gradient(ellipse at 55% 50%, rgba(190, 150, 130, 0.55), transparent 55%),
      radial-gradient(ellipse at 10% 40%, rgba(110, 60, 50, 0.6), transparent 50%),
      linear-gradient(90deg, var(--photo-warm) 0%, #3a2c2c 55%, var(--photo-dark) 100%);
  }
  .frame {
    position: absolute;
    left: 0;
    top: 0;
  }
  .page-number {
    position: absolute;
    left: 1170px;
    top: 326px;
    font-family: "Open Sans", sans-serif;
    font-weight: 600;
    font-size: 18px;
    color: var(--gold);
  }
  .content {
    position: absolute;
    left: 694px;
    top: 330px;
    width: 420px;
  }
  .title {
    font-family: "Raleway", sans-serif;
    font-weight: 400;
    font-size: 38px;
    line-height: 1.2;
    color: var(--gold);
    white-space: nowrap;
  }
  .body-text {
    margin-top: 30px;
    font-family: "Open Sans", sans-serif;
    font-weight: 400;
    font-size: 20px;
    line-height: 32px;
    color: var(--text-light);
  }
</style>
</head>
<body>
  <div class="slide">
    <div class="hero-photo" role="img" aria-label="Close-up photo of a hand aiming a dart toward the viewer"></div>

    <svg class="frame" width="1200" height="675" viewBox="0 0 1200 675" aria-hidden="true">
      <defs>
        <linearGradient id="frame-vertical" x1="0" y1="0" x2="0" y2="1">
          <stop offset="0" stop-color="#f5b300" stop-opacity="0"/>
          <stop offset="0.35" stop-color="#f5b300" stop-opacity="0.75"/>
          <stop offset="1" stop-color="#ffd45a"/>
        </linearGradient>
        <linearGradient id="frame-horizontal" x1="0" y1="0" x2="1" y2="0">
          <stop offset="0" stop-color="#f5b300" stop-opacity="0"/>
          <stop offset="0.5" stop-color="#f5b300" stop-opacity="0.8"/>
          <stop offset="1" stop-color="#ffd45a"/>
        </linearGradient>
      </defs>
      <rect x="1134" y="122" width="5" height="503" fill="url(#frame-vertical)"/>
      <rect x="618" y="620" width="521" height="5" fill="url(#frame-horizontal)"/>
    </svg>

    <div class="page-number">5</div>

    <div class="content">
      <h1 class="title">The “elevator pitch”</h1>
      <p class="body-text">Skip the technical details about your product. If investors leave the meeting and can’t remember your pitch, you’ve failed.</p>
    </div>
  </div>
</body>
</html>
```